Volunteer fire fighters needed banner

As part of our recruitment campaign, we need a sign we can post on our sign trailer to entice locals to join our volunteer fire service. This design will be printed on a banner, front and back, to catch traffic going in both directions on a busy roadway. This banner will have a printed surface of 4 feet tall by 8 feet long.
Our fire department is looking to attract people between the ages of 18 and 35 years old who are interested in being a firefighter. We offer our volunteers:
-Free professional training
-All equipment supplied
-Tax abatements for active volunteers
For more information, you can check us out at:
Brackenmoorfire.example

This design should:
-scale to and fit a 4'x8' canvas
-Include our web address "BrackenMoorFire.example"
-Say "Members Wanted"
-"Drill every Tuesday at 7pm"
-"57 Kestrel Pond Lane"
-Include "Bracken Moor Fire Department"

We've included reference photos and past images we use for our other campaigns for inspiration for you.

Target Market(s)

18-35 y/o

Industry/Entity Type

Fire Service

Requirements
Must have
• -scale to and fit a 4'x8' canvas -Include our web address "BrackenMoorFire.example" -Say "Members Wanted" -"Drill every Tuesday at 7pm" -"57 Kestrel Pond Lane" -Include "Bracken Moor Fire Department"

```html
<!DOCTYPE html>
<html lang="en">
<head>
<meta charset="utf-8">
<title>Bracken Moor Fire Department – Recruitment Banner</title>
<link rel="stylesheet" href="https://fonts.googleapis.com/css2?family=Montserrat:wght@700;800;900&display=swap">
<style>
  :root {
    --page-bg: #e9eaee;
    --banner-bg: #515373;
    --banner-bg-dark: #44465f;
    --band-navy: #27346b;
    --frame-gold: #f2b31b;
    --accent-red: #e0262b;
    --text-white: #ffffff;
  }
  * { margin: 0; padding: 0; box-sizing: border-box; }
  html, body {
    width: 1200px; height: 1200px; overflow: hidden;
    background: var(--page-bg);
    font-family: "Montserrat", Arial, sans-serif;
  }
  .banner {
    position: absolute; left: 40px; top: 320px;
    width: 1120px; height: 560px;
    background: radial-gradient(ellipse at 35% 40%, var(--banner-bg) 0%, var(--banner-bg-dark) 100%);
    overflow: hidden; color: var(--text-white);
  }
  .hero-figure {
    position: absolute; left: 300px; top: 0; width: 420px; height: 560px;
    background: linear-gradient(180deg, rgba(150,70,80,0.35) 0%, rgba(90,92,115,0.45) 35%, rgba(70,72,92,0.5) 100%);
    opacity: 0.8;
  }
  .org-name {
    position: absolute; left: 40px; top: 30px;
    display: flex; align-items: center; gap: 10px;
    font-weight: 800; font-size: 17px; letter-spacing: 0.5px;
  }
  .org-name .dot { width: 16px; height: 16px; border-radius: 50%; background: var(--accent-red); }
  .headline {
    position: absolute; left: 40px; top: 78px;
    font-weight: 900; font-size: 104px; line-height: 0.93;
    text-transform: uppercase; letter-spacing: -1px;
  }
  .drill-band {
    position: absolute; left: 34px; top: 384px;
    background: var(--band-navy);
    padding: 8px 18px;
    font-weight: 800; font-size: 31px; text-transform: uppercase;
  }
  .web-address {
    position: absolute; left: 40px; bottom: 38px;
    display: flex; align-items: center; gap: 12px;
    font-weight: 800; font-size: 29px; text-transform: uppercase;
  }
  .web-address svg { width: 32px; height: 32px; }
  .side-mark {
    position: absolute; right: 30px; top: 34px;
    display: flex; align-items: center; gap: 8px;
    font-weight: 800; font-size: 14px; text-transform: uppercase;
  }
  .side-mark .dot { width: 12px; height: 12px; border-radius: 50%; background: var(--accent-red); }
  .members-line {
    position: absolute; left: 700px; width: 392px; top: 138px;
    text-align: center;
    font-weight: 800; font-size: 36px; text-transform: uppercase;
  }
  .crew-photo {
    position: absolute; left: 700px; top: 200px; width: 392px; height: 296px;
    border: 5px solid var(--frame-gold); border-radius: 34px;
    background: linear-gradient(160deg, #3b3a36 0%, #2a2a28 55%, #4a4b3a 100%);
  }
  .address {
    position: absolute; right: 30px; bottom: 22px;
    display: flex; align-items: center; gap: 8px;
    font-weight: 800; font-size: 25px; text-transform: uppercase;
  }
  .address svg { width: 18px; height: 26px; }
</style>
</head>
<body>
  <section class="banner">
    <div class="hero-figure" role="img" aria-label="Faded photo of a firefighter in helmet carrying an axe over the shoulder"></div>

    <div class="org-name"><span class="dot"></span>Bracken Moor Fire Department</div>

    <h1 class="headline">Local<br>Heroes<br>Wanted</h1>

    <div class="drill-band">Drill every Tuesday at 7pm</div>

    <div class="web-address">
      <svg viewBox="0 0 32 32" aria-hidden="true">
        <circle cx="16" cy="16" r="15" fill="var(--accent-red)"/>
        <g fill="none" stroke="#fff" stroke-width="1.8">
          <circle cx="16" cy="16" r="9"/>
          <ellipse cx="16" cy="16" rx="4" ry="9"/>
          <line x1="7" y1="16" x2="25" y2="16"/>
        </g>
      </svg>
      <span>BrackenMoorFire.example</span>
    </div>

    <div class="side-mark"><span class="dot"></span>Bracken Moor</div>

    <h2 class="members-line">Members Wanted</h2>

    <div class="crew-photo" role="img" aria-label="Photo of three volunteer firefighters in turnout gear"></div>

    <div class="address">
      <svg viewBox="0 0 18 26" aria-hidden="true">
        <path d="M9 1C4.6 1 1 4.6 1 9c0 6 8 16 8 16s8-10 8-16c0-4.4-3.6-8-8-8z" fill="var(--accent-red)"/>
        <circle cx="9" cy="9" r="3" fill="#fff"/>
      </svg>
      <span>57 Kestrel Pond Lane</span>
    </div>
  </section>
</body>
</html>
```